Before the kettle boils, pocast with content in its majority of technology

Page dedicated to a pocast with content in its majority of technology. The page also contains the chapters of the podcast (pluggin vocalink) will also contain news. Preferably Worpress. There is already a very basic page with a simple theme, the logo and little more, I would like something more professional. Www.lamparadebolsillo.com The logo does not want to change.

Target Market(s)

Anyone

Colors

Designer to choose colors to be used in the design.

Requirements
Must have
• You can put the vocalink pluggin with the podcast chapters

```html
<!DOCTYPE html>
<html lang="es">
<head>
<meta charset="utf-8">
<title>Before the kettle boils — podcast</title>
<link href="https://fonts.googleapis.com/css2?family=Roboto:wght@400;500;700&family=Roboto+Condensed:wght@400;700&display=swap" rel="stylesheet">
<style>
:root{
  --page:#1f1f1f;
  --header:#151515;
  --card:#ffffff;
  --orange:#f07a1e;
  --orange-dark:#d9640c;
  --text:#555555;
  --title:#2b2b2b;
  --muted:#9a9a9a;
  --line:#e6e6e6;
  --widget:#2a2a2a;
  --widget-head:#333333;
  --widget-text:#d8d8d8;
  --green:#2bb673;
  --player:#f5f5f5;
}
*{box-sizing:border-box;margin:0;padding:0}
html,body{width:1200px;height:4215px;overflow:hidden}
body{background:var(--page);font-family:"Roboto",Arial,sans-serif;color:var(--text);position:relative}
.site-header{height:140px;background:linear-gradient(180deg,#202020,var(--header));position:relative}
.brand{position:absolute;left:130px;top:14px;display:flex;align-items:center;gap:12px}
.brand-mark{width:56px;height:56px;border-radius:50%;background:var(--orange)}
.brand-name{font-family:"Roboto Condensed",Arial,sans-serif;font-weight:700;font-size:19px;color:var(--orange);text-transform:uppercase;letter-spacing:.5px;line-height:1.1;width:170px}
.header-social{position:absolute;right:115px;top:20px;display:flex;gap:8px}
.header-social span{width:32px;height:32px;border-radius:50%;border:2px solid #fff}
.header-actions{position:absolute;right:110px;top:82px;display:flex;gap:14px}
.btn{height:32px;padding:0 22px;font-size:12px;font-weight:700;color:#fff;display:flex;align-items:center;text-transform:uppercase}
.btn-dark{background:#2b2b2b}
.btn-orange{background:var(--orange)}

.main{position:absolute;left:112px;top:196px;width:725px}
.post{background:var(--card);position:relative;margin-bottom:34px;box-shadow:0 2px 6px rgba(0,0,0,.4)}
.post-head{height:72px;border-bottom:1px solid var(--line);position:relative;padding-left:104px;padding-top:16px}
.date-badge{position:absolute;left:-6px;top:8px;width:96px;height:60px;background:var(--orange);color:#fff;display:flex;align-items:center;padding-left:10px;gap:6px}
.date-badge b{font-family:"Roboto Condensed",sans-serif;font-size:34px;font-weight:700}
.date-badge small{font-size:11px;font-weight:700;line-height:1.1;text-transform:uppercase}
.post-title{font-family:"Roboto Condensed",sans-serif;font-size:21px;font-weight:700;color:var(--title)}
.author{font-size:10px;font-weight:700;color:var(--orange);margin-top:6px;text-transform:uppercase}
.comments{position:absolute;right:18px;top:12px;width:50px;height:50px;border-radius:50%;border:2px solid var(--line);color:var(--orange);font-size:11px;display:flex;align-items:center;justify-content:center}
.post-body{padding:18px 30px 10px;font-size:12.5px;line-height:1.65}
.post-body p{margin-bottom:14px}
.post-foot{height:50px;border-top:1px solid var(--line);display:flex;align-items:center;justify-content:space-between;padding:0 30px;font-size:10.5px;color:var(--muted)}
.share{display:flex;align-items:center;gap:8px;font-weight:700;color:#444;font-size:10px;text-transform:uppercase}
.share-dots{display:flex;gap:5px}
.share-dots span{width:20px;height:20px;border-radius:50%;background:#8a8a8a}

.prices{border:1px solid var(--line);padding:18px 24px;display:flex;gap:18px;margin-bottom:16px}
.plan{flex:1;border:1px solid var(--line);text-align:center;font-size:11px}
.plan-top{display:flex;align-items:center;justify-content:center;gap:8px;padding:10px 0;color:var(--green)}
.plan-top b{font-size:24px;font-weight:400}
.plan-price{padding:12px 0 6px;font-size:22px;color:#333}
.plan-old{font-size:11px;color:#aaa;text-decoration:line-through;height:16px}
.plan-band{background:var(--green);color:#fff;font-size:10px;padding:6px 0;margin-top:8px}
.plan-radio{width:14px;height:14px;border-radius:50%;border:1px solid #bbb;margin:10px auto}
.plan-radio.on{border:4px solid #1a73c7}

.player{display:flex;background:var(--player);height:230px;margin:10px 0 16px;border:1px solid #ececec}
.player-main{flex:1;padding:22px 20px;position:relative}
.play{width:80px;height:80px;border-radius:50%;background:#f5b400;position:absolute;left:20px;top:22px}
.play svg{position:absolute;left:30px;top:24px}
.player-title{margin-left:100px;font-size:20px;color:#222;line-height:1.3;width:250px}
.player-label{position:absolute;right:18px;top:20px;font-size:14px;font-weight:700;color:#333}
.player-meta{margin-left:100px;font-size:12px;color:#333;margin-top:6px}
.times{position:absolute;left:20px;right:18px;top:128px;display:flex;justify-content:space-between;font-size:11px;color:#777}
.wave{position:absolute;left:20px;right:18px;bottom:18px;height:62px;background:linear-gradient(0deg,#cfcfcf,#e8e8e8)}
.player-art{width:230px}

.sidebar{position:absolute;left:866px;top:208px;width:224px}
.search{height:40px;background:var(--widget);border:1px solid #3a3a3a;padding:10px;font-size:12px;color:#777;margin-bottom:44px}
.widget{background:var(--widget);margin-bottom:44px;font-size:12px;color:var(--widget-text)}
.widget h3{background:var(--widget-head);color:#fff;font-size:16px;font-weight:700;padding:16px 22px}
.widget ul{list-style:none;padding:12px 22px}
.widget li{padding:7px 0;line-height:1.4}
.archives li::before{content:"▸ ";color:#999}
.contact li{display:flex;align-items:center;gap:10px}
.contact li i{width:10px;height:10px;background:#999;border-radius:2px}

.pager{position:absolute;left:300px;top:3952px;display:flex;gap:6px;font-size:11px}
.pager span{height:28px;min-width:28px;padding:0 10px;border-radius:14px;background:#333;color:#ccc;display:flex;align-items:center;justify-content:center}
.pager span.on{background:var(--orange);color:#fff}
.site-footer{position:absolute;left:0;top:4060px;width:100%;text-align:center}
.foot-social{display:flex;gap:10px;justify-content:center}
.foot-social span{width:34px;height:34px;border-radius:50%;background:#2d6fb3}
.foot-social span:nth-child(2){background:#2ba0d8}
.foot-social span:nth-child(3){background:#d54434}
.copy{font-size:11px;color:#888;margin-top:28px;line-height:1.6}
</style>
</head>
<body>
<header class="site-header">
  <div class="brand"><span class="brand-mark"></span><span class="brand-name">Before the kettle boils</span></div>
  <div class="header-social"><span></span><span></span><span></span></div>
  <div class="header-actions"><span class="btn btn-dark">Register</span><span class="btn btn-orange">Login</span></div>
</header>

<main class="main">
  <article class="post">
    <div class="post-head">
      <div class="date-badge"><b>19</b><small>May<br>2017</small></div>
      <h2 class="post-title">Cambio de logo</h2>
      <div class="comments">229</div>
    </div>
    <div class="post-body" style="height:220px">
      <p>Hola a Tod@s!</p>
      <p>¿Salta a la vista no?, pues sí, renovamos diseño del logo y algo en la web. Aquí los cambios irán poco a poco pero procuraré dejar todo lo que quiero modificar hecho en una semana (como mucho, todo dependerá del tiempo que le pueda dedicar aunque lo difícil ya está hecho.</p>
      <p>Nada más, nos escuchamos en el siguiente!</p>
    </div>
    <div class="post-foot">
      <div class="share-dots"><span></span><span></span><span></span><span></span><span></span><span></span><span></span><span></span><span></span><span></span><span></span></div>
      <span>Publicado en Sin categoría | Deja un comentario</span>
    </div>
  </article>

  <article class="post">
    <div class="post-head">
      <div class="date-badge"><b>17</b><small>May<br>2017</small></div>
      <h2 class="post-title">¿Te gustan las series?¿Conoces serimundo.tv?</h2>
      <div class="author">De rafelo</div>
      <div class="comments">229</div>
    </div>
    <div class="post-body">
      <p>Hola a tod@s!</p>
      <p>Hoy capítulo dedicado a los amantes de las series y las películas. Se trata del servicio de vídeo en streaming de la web serimundo.tv portal dedicado al aprendizaje de inglés mediante el método de ver películas y series en inglés con subtítulos.</p>
      <p>El catálogo es muy amplio, actual y completo. Están prácticamente todas las series de la actualidad al día y los clásicos más famosos. Te puedes registrar desde una cuenta de correo o redes sociales, rápido y sencillo. Hay opciones gratuitas (límite de 60 minutos al día) y de pago, donde se elimina el límite de minutos y permite descargas. Estos son los precios:</p>
      <div class="prices">
        <div class="plan"><div class="plan-top"><b>1</b>mes</div><div class="plan-price">6 €</div><div class="plan-old"></div><div class="plan-band">base</div><div class="plan-radio"></div></div>
        <div class="plan"><div class="plan-top"><b>3</b>meses</div><div class="plan-price">16 €</div><div class="plan-old">18 €</div><div class="plan-band">descuento de 11%</div><div class="plan-radio on"></div></div>
        <div class="plan"><div class="plan-top"><b>6</b>meses</div><div class="plan-price">28 €</div><div class="plan-old">36 €</div><div class="plan-band">descuento de 22%</div><div class="plan-radio"></div></div>
        <div class="plan"><div class="plan-top"><b>12</b>meses</div><div class="plan-price">48 €</div><div class="plan-old">72 €</div><div class="plan-band">descuento de 33%</div><div class="plan-radio"></div></div>
      </div>
      <p>Es fácil conseguir descuentos sobre todo en la cuenta anual, actualmente están ofreciendo 2 años por 40€ en lugar de un año. Buscadlo por la red y veréis.</p>
      <p>En el catálogo entran todas las plataformas actuales, hay series de Flixnet, CanalNorte, Primavid, etc. En una búsqueda rápida no echarás de menos ninguna serie.</p>
      <p>Por ponerle una pega, no tiene aplicación de dispositivo móvil aunque no le haga falta, es híbrida y desde cualquier navegador de un dispositivo móvil funciona muy bien y se puede poner a pantalla completa.</p>
      <p>Es gratis probadla y veréis.</p>
      <p>Nos escuchamos en el siguiente.</p>
      <div class="player">
        <div class="player-main">
          <div class="play"><svg width="26" height="32"><polygon points="0,0 26,16 0,32" fill="#fff"/></svg></div>
          <div class="player-title">¿Te gustan las series?¿Conoces serimundo.tv?</div>
          <div class="player-meta">♥ 1 &nbsp; ➤ &nbsp; ●</div>
          <div class="player-label">vocalink</div>
          <div class="times"><span>00:00</span><span>10:58</span></div>
          <div class="wave"></div>
        </div>
        <div class="player-art" role="img" aria-label="Collage de carteles de series" style="background:linear-gradient(135deg,#3a2a22,#6a4a3a 50%,#1e2a3a)"></div>
      </div>
    </div>
    <div class="post-foot"><span class="share">➦ Compartir</span><span>Publicado en Sin categoría | Deja un comentario</span></div>
  </article>

  <article class="post">
    <div class="post-head">
      <div class="date-badge"><b>23</b><small>Nov<br>2016</small></div>
      <h2 class="post-title">Seguridad en tu Mail</h2>
      <div class="author">De rafelo</div>
      <div class="comments">229</div>
    </div>
    <div class="post-body">
      <p>¡Hola a todos!</p>
      <p>Hoy poco más que decir por aquí de lo dicho en el podcast. Para aquellos que necesiten un punto más de seguridad en el correo electrónico está SobreCerrado. Planes gratuitos y de pago, codificación, mensajes que se pueden auto destruir, etc.</p>
      <p>SobreCerrado</p>
      <p>Un saludo, nos escuchamos en el siguiente.</p>
      <div class="player">
        <div class="player-main">
          <div class="play"><svg width="26" height="32"><polygon points="0,0 26,16 0,32" fill="#fff"/></svg></div>
          <div class="player-title">Seguridad en tu Mail</div>
          <div class="player-meta">♥ 1 &nbsp; ➤ &nbsp; ●</div>
          <div class="player-label">vocalink</div>
          <div class="times"><span>00:00</span><span>09:53</span></div>
          <div class="wave"></div>
        </div>
        <div class="player-art" role="img" aria-label="Portada del episodio sobre correo seguro" style="background:#3f3f74"></div>
      </div>
    </div>
    <div class="post-foot"><span class="share">➦ Compartir</span><span>Publicado en Sin categoría | Deja un comentario</span></div>
  </article>

  <article class="post">
    <div class="post-head">
      <div class="date-badge"><b>20</b><small>Nov<br>2016</small></div>
      <h2 class="post-title">Kiomi TabPad2, calidad precio insuperable</h2>
      <div class="author">De rafelo</div>
      <div class="comments">229</div>
    </div>
    <div class="post-body">
      <p>Con un poco de retraso publicamos el post del podcast de la tableta de Kiomi. Tableta que como viene siendo habitual de la marca, da mucho más de lo que cuesta.</p>
      <p>Os lo comento más detalladamente en el podcast pero es una tableta con un chip de cuatro núcleos, que permite la instalación de dos sistemas operativos, 2 Gb de RAM, almacenamiento de 16 o 64, 7,9 pulgadas en una fantástica pantalla, que la hacen cumplir más que de sobra en su funcionamiento y a un precio muy apetecible.</p>
      <p>Además como en mi caso, no es raro conseguir un cupón de descuento para poder adquirirla a un mejor precio.</p>
      <p>Si tenéis cualquier duda os lo respondo en los comentarios.</p>
      <p>Un saludo y nos escuchamos en el siguiente</p>
      <div class="player">
        <div class="player-main">
          <div class="play"><svg width="26" height="32"><polygon points="0,0 26,16 0,32" fill="#fff"/></svg></div>
          <div class="player-title">Kiomi TabPad2, calidad precio insuperable</div>
          <div class="player-meta">♥ 2 &nbsp; ➤ &nbsp; ●</div>
          <div class="player-label">vocalink</div>
          <div class="times"><span>00:00</span><span>25:31</span></div>
          <div class="wave"></div>
        </div>
        <div class="player-art" role="img" aria-label="Portada naranja del episodio de la tableta" style="background:#f26a1b"></div>
      </div>
    </div>
    <div class="post-foot"><span class="share">➦ Compartir</span><span>Publicado en Sin categoría | Deja un comentario</span></div>
  </article>

  <article class="post">
    <div class="post-head">
      <div class="date-badge"><b>20</b><small>Jul<br>2016</small></div>
      <h2 class="post-title">Podcast futuros, vocalink, seriere recomendada</h2>
      <div class="author">De rafelo</div>
      <div class="comments">229</div>
    </div>
    <div class="post-body">
      <p>Podcast de hoy variado, un adelanto de uno o una serie (ya veremos) de podcast que voy a grabar en un futuro, opinión de los nuevos planes de precios de vocalink y la recomendación de una serie Los Restantes.</p>
      <p>Como ya os comento en el podcast el tema Notaverde está ya muy adelantado, solo falta determinar el formato, uno más largo 2 cortos, uno a cada aplicación... Ya veremos.</p>
      <p>Tema vocalink, hay subida de precios y cambios en las cuentas gratuitas como la mía; menos horas de alojamiento de los podcast, se reducen de la mitad de horas y las cuentas premium aumentan de precio. Yo seguiré igual, cuenta gratuita cuando sea necesario se borrarán podcast, el feed debe de seguir y no me apetece de momento estar haciendo cambios. Los podcast también se suben a otra plataforma, así que si necesitáis alguno que se haya borrado, allí los tenéis.</p>
      <p>Los Restantes, primera temporada suuuuuum buena, de menos a más, pero la segunda es una maravilla, merece ver la serie para ver esa segunda temporada (y que la primera tampoco está mal). Otra recomendación es su banda sonora.</p>
      <p>Y poco más, nos escuchamos en el siguiente.</p>
      <div class="player">
        <div class="player-main">
          <div class="play"><svg width="26" height="32"><polygon points="0,0 26,16 0,32" fill="#fff"/></svg></div>
          <div class="player-title">Podcast futuros, vocalink, serie recomendada</div>
          <div class="player-meta">♥ 1 &nbsp; ➤ &nbsp; ●</div>
          <div class="player-label">vocalink</div>
          <div class="times"><span>00:00</span><span>13:20</span></div>
          <div class="wave"></div>
        </div>
        <div class="player-art" role="img" aria-label="Escena submarina en tonos azules" style="background:linear-gradient(180deg,#4f8fa8,#173548)"></div>
      </div>
    </div>
    <div class="post-foot"><span class="share">➦ Compartir</span><span>Publicado en Sin categoría | Deja un comentario</span></div>
  </article>
</main>

<aside class="sidebar">
  <div class="search">Buscar...</div>
  <section class="widget">
    <h3>Recent Posts</h3>
    <ul>
      <li>Cambio de logo</li>
      <li>¿Te gustan las series?¿Conoces serimundo.tv?</li>
      <li>Un anuncio y una prueba</li>
      <li>Seguridad en tu Mail</li>
      <li>Kiomi TabPad2, calidad precio insuperable</li>
    </ul>
  </section>
  <section class="widget contact">
    <h3>Contacto</h3>
    <ul>
      <li><i></i>Microblog</li>
      <li><i></i>vocalink</li>
      <li><i></i>Feed</li>
      <li><i></i>Mail</li>
    </ul>
  </section>
  <section class="widget archives">
    <h3>Archives</h3>
    <ul>
      <li>May 2017</li><li>April 2017</li><li>March 2017</li><li>February 2017</li><li>January 2017</li>
      <li>December 2016</li><li>November 2016</li><li>October 2016</li><li>September 2016</li><li>August 2016</li>
      <li>July 2016</li><li>June 2016</li><li>May 2016</li><li>April 2016</li><li>March 2016</li>
      <li>February 2016</li><li>January 2016</li>
    </ul>
  </section>
</aside>

<nav class="pager"><span>« Prev</span><span class="on">01</span><span>02</span><span>03</span><span>05</span><span>06</span><span>Next »</span></nav>

<footer class="site-footer">
  <div class="foot-social"><span></span><span></span><span></span></div>
  <p class="copy">Copyright © 2017 Before the kettle boils. All Rights Reserved.<br>Terms of Use &nbsp;|&nbsp; Privacy Policy &nbsp;|&nbsp; Sitemap</p>
</footer>
</body>
</html>
```